TK Stationery - Modern Contemporary

Develop modern template for Letterhead and Stationery (business card, letterhead, envelopes) using the TK Logo and Icon

Colors
0054AA
0677BA
7BADD7
CADEEF
E8F1F8
00AB8E
00BBA5
67D7C9
C6EFE9
E9F9F6
EE7325
F08F49
F5BC92
FAE3D3
FDF4ED
6B429C
8869AF
B7A5CE
E3DAEB
F3F0F8

```html
<!DOCTYPE html>
<html lang="en">
<head>
<meta charset="utf-8">
<title>Talo Kestrel – Business Card</title>
<link rel="stylesheet" href="https://fonts.googleapis.com/css2?family=Arimo:wght@400;700&display=swap">
<style>
  :root {
    --backdrop: #1c1c1c;
    --brand-blue: #0054aa;
    --brand-teal: #00ab8e;
    --pale-teal: #c6efe9;
    --white: #ffffff;
    --card-w: 680px;
    --card-h: 388px;
  }
  * { box-sizing: border-box; margin: 0; padding: 0; }
  html, body { width: 1200px; height: 1015px; overflow: hidden; }
  body {
    background: var(--backdrop);
    font-family: "Arimo", Arial, sans-serif;
    position: relative;
  }
  .card {
    position: absolute;
    left: 260px;
    width: var(--card-w);
    height: var(--card-h);
    overflow: hidden;
    box-shadow: 0 12px 30px rgba(0,0,0,.55);
  }
  .card--front { top: 80px; background: var(--brand-blue); }
  .card--back { top: 548px; background: var(--white); }

  .band {
    position: absolute;
    left: 0; right: 0;
    height: 38px;
    background: var(--brand-teal);
    display: flex;
    align-items: center;
    color: var(--white);
    font-size: 17px;
    letter-spacing: .5px;
  }
  .card--front .band { top: 270px; justify-content: center; }
  .card--back .band { top: 300px; padding-left: 408px; }

  .wordmark {
    position: absolute;
    font-size: 42px;
    font-weight: 400;
    letter-spacing: 1px;
    white-space: nowrap;
  }
  .card--front .wordmark { color: var(--white); left: 50%; top: 128px; transform: translateX(-50%); }
  .card--back .wordmark { color: var(--brand-blue); left: 150px; top: 130px; transform: translateX(-50%); font-size: 34px; }

  .info-panel {
    position: absolute;
    left: 300px; top: 0;
    width: 380px; height: 100%;
    background: var(--brand-blue);
    color: var(--white);
    padding: 70px 30px 0 44px;
  }
  .info-panel__name {
    color: var(--pale-teal);
    font-weight: 700;
    font-size: 21px;
    letter-spacing: .5px;
  }
  .info-panel__title { font-size: 15px; margin-top: 2px; }
  .contact { list-style: none; margin-top: 22px; font-size: 15px; }
  .contact li { display: flex; align-items: center; gap: 9px; margin-bottom: 6px; }
  .contact svg { width: 16px; height: 16px; flex: none; }
  .address { font-size: 15px; line-height: 1.35; margin-top: 18px; }
</style>
</head>
<body>

<section class="card card--front">
  <p class="wordmark">talo kestrel</p>
  <div class="band"><span class="url">www.talokestrel.com</span></div>
</section>

<section class="card card--back">
  <p class="wordmark">talo kestrel</p>
  <div class="info-panel">
    <p class="info-panel__name">DANIEL HARPER</p>
    <p class="info-panel__title">Managing Director</p>
    <ul class="contact">
      <li>
        <svg viewBox="0 0 24 24" aria-hidden="true"><path fill="#c6efe9" d="M6.6 10.8a15.1 15.1 0 0 0 6.6 6.6l2.2-2.2a1 1 0 0 1 1-.25 11.4 11.4 0 0 0 3.6.57 1 1 0 0 1 1 1V20a1 1 0 0 1-1 1A17 17 0 0 1 3 4a1 1 0 0 1 1-1h3.5a1 1 0 0 1 1 1c0 1.25.2 2.45.57 3.57a1 1 0 0 1-.25 1z"/></svg>
        <span>044-555 010 220</span>
      </li>
      <li>
        <svg viewBox="0 0 24 24" aria-hidden="true"><path fill="#c6efe9" d="M2 5h20v14H2z"/><path fill="none" stroke="#0054aa" stroke-width="1.6" d="M2 5l10 8 10-8"/></svg>
        <span>hello@talokestrel.com</span>
      </li>
    </ul>
    <p class="address">18, Harbour Lane, Riverside<br>20410, Northland</p>
  </div>
  <div class="band"><span class="url">www.talokestrel.com</span></div>
</section>

</body>
</html>
```